Vostrellen - online education agent and consultancy

Online education provider for business to business market needs a dynamic, modern and mobile friendly website. We have the shell view www.quorvana.com but it is boring!
I will need to add courses to the website - Business, Health and Wellbeing, Digital, Aviation.
I am targeting mainly services based industries - so blue collar workers, living in the outer suburbs, will be studying online and most likely from home.
They need to feel safe and secure - we are reputable and importantly can support them all the way to course completion.
What makes us stand out from everyone else - we dont offer any courses - we pick and choose the best courses, with the best providers and only offer quality.
We take the time to find out what the student really wants to achieve and match them with the right education provider.

Target Market(s)

Business to Business - HR managers, People and Culture Managers, employees who are 25+ years currently working wanting to further their careers with accredited qualifications

Industry/Entity Type

Education

Number of Pages Required

5+ page

Font styles to use
Sans Serif

Colors
00a990
acd036
0792cd
a54499
f37122

Requirements
Must have
• Mobile functionality - view on ovulet/ovutab
• Home page
• Courses section
• Contact us
• Payment checkout to be added
Nice to have
• Fresh, inviting, images that reflect the difference we will make - supporting people through the whole journey.
• It needs to be inviting - homely but modern
Should not have
• Black, dark colours

```html
<!DOCTYPE html>
<html lang="en">
<head>
<meta charset="utf-8">
<title>Quorvana – Payment</title>
<link href="https://fonts.googleapis.com/css2?family=Raleway:wght@400;500&family=Open+Sans:wght@400&display=swap" rel="stylesheet">
<style>
:root{
  --green-top:#bcdc4c;
  --green-bottom:#8ec21f;
  --blue:#0a91cf;
  --orange-top:#f6b40a;
  --orange-bottom:#e38b00;
  --phone-orange:#f7941d;
  --ink:#222;
  --label:#444;
  --muted:#999;
  --field-border:#c8c8c8;
  --white:#fff;
}
*{box-sizing:border-box;margin:0;padding:0}
html,body{width:1200px;height:1019px;overflow:hidden;background:var(--white)}
.page{position:relative;width:1200px;height:1019px;font-family:'Open Sans',sans-serif;color:var(--label)}
.abs{position:absolute}

.brand{left:456px;top:40px;width:300px;display:flex;align-items:center;justify-content:center;gap:10px}
.brand-dot{flex:0 0 24px;width:24px;height:24px;border-radius:50%;background:var(--green-bottom)}
.brand-name{font-family:'Raleway',sans-serif;font-weight:400;font-size:44px;letter-spacing:3px;color:var(--green-bottom);white-space:nowrap}

.phone{left:910px;top:79px;display:flex;align-items:center;gap:6px;font-family:'Raleway',sans-serif;font-weight:500;font-size:20px;font-variant-numeric:lining-nums;color:#444}
.phone-icon{width:30px;height:30px;flex:0 0 30px}

.main-nav{left:0;top:127px;width:1200px;height:58px;background:linear-gradient(var(--green-top),var(--green-bottom))}
.main-nav a{position:absolute;top:0;height:58px;line-height:58px;transform:translateX(-50%);font-family:'Raleway',sans-serif;font-weight:500;font-size:18px;color:var(--white);text-decoration:none;white-space:nowrap}
.nav-sep{position:absolute;top:0;width:1px;height:58px;background:rgba(255,255,255,.45)}

.page-title{left:146px;top:250px;font-family:'Raleway',sans-serif;font-weight:400;font-size:23px;color:var(--ink)}

.label{left:146px;font-size:14px;color:var(--label);transform:translateY(-50%);white-space:nowrap}
.field{border:1px solid var(--field-border);background:linear-gradient(#fafafa,#ececec);border-radius:2px;font-size:12px;color:var(--muted);display:flex;align-items:center;justify-content:center}
.field.select{justify-content:space-between;padding:0 12px}
.caret{width:0;height:0;border-left:6px solid transparent;border-right:6px solid transparent;border-top:8px solid #888}

.card{width:37px;height:26px;border:1px solid #ddd;background:#f7f7f7;border-radius:2px;font-size:6.5px;color:#1c4a8f;display:flex;align-items:center;justify-content:center;white-space:nowrap;overflow:hidden}

.btn{background:linear-gradient(var(--orange-top),var(--orange-bottom));color:var(--white);font-family:'Raleway',sans-serif;font-weight:400;font-size:15.5px;display:flex;align-items:center;justify-content:center;border-radius:2px}

.divider{left:669px;top:319px;width:1px;height:296px;background:#ccc}
.side-title{left:707px;top:317px;font-family:'Raleway',sans-serif;font-weight:400;font-size:18.5px;color:var(--ink);white-space:nowrap}
.side-label{font-size:14px;color:var(--label)}
.forgot{left:712px;top:547px;font-size:13px;color:#555;border-bottom:1px solid #999;line-height:16px}

.footer{left:0;top:899px;width:1200px;height:120px;background:var(--blue);color:var(--white)}
.footer-nav a{position:absolute;top:34px;font-family:'Raleway',sans-serif;font-weight:500;font-size:14.5px;color:var(--white);text-decoration:none;white-space:nowrap}
.copyright{position:absolute;left:127px;top:65px;font-size:11.5px;white-space:nowrap}
.social{position:absolute;left:936px;top:39px;display:flex;gap:12px}
.social span{width:20px;height:20px;border-radius:50%;background:var(--white)}
</style>
</head>
<body>
<div class="page">

  <div class="abs brand"><span class="brand-dot"></span><span class="brand-name">QUORVANA</span></div>

  <div class="abs phone">
    <svg class="phone-icon" viewBox="0 0 30 30"><circle cx="15" cy="15" r="15" fill="var(--phone-orange)"/><path d="M10 9c1-1 2-1 3 0l1.5 2c.5.8.3 1.5-.3 2l-.8.7c.7 1.6 2 3 3.6 3.7l.7-.8c.5-.6 1.3-.8 2-.3l2 1.5c1 .8 1 2 0 3-1.4 1.4-3.5 1.6-5.8.2-2.5-1.5-4.7-3.8-6-6.3C8.6 12.5 8.7 10.4 10 9z" fill="none" stroke="#fff" stroke-width="1.5"/></svg>
    <span>1300 55 41 82</span>
  </div>

  <nav class="abs main-nav">
    <a style="left:221px" href="#">HOME</a>
    <span class="nav-sep" style="left:278px"></span>
    <a style="left:380px" href="#">VOSTRELLEN</a>
    <span class="nav-sep" style="left:477px"></span>
    <a style="left:577px" href="#">OUR COURSES</a>
    <span class="nav-sep" style="left:671px"></span>
    <a style="left:756px" href="#">LET'S CHAT</a>
    <span class="nav-sep" style="left:838px"></span>
    <a style="left:937px" href="#">ABOUT QUORVANA</a>
  </nav>

  <h1 class="abs page-title">Payment with Credit Card or Log In</h1>

  <span class="abs label" style="top:340px">Country</span>
  <div class="abs field select" style="left:297px;top:324px;width:331px;height:31px"><span>Select Country</span><span class="caret"></span></div>

  <span class="abs label" style="top:380px">Credit Card Number</span>
  <div class="abs field" style="left:297px;top:365px;width:331px;height:31px"></div>

  <span class="abs label" style="top:460px">Payment Type</span>
  <div class="abs card" style="left:293px;top:446px">VELRA</div>
  <div class="abs card" style="left:343px;top:446px">AMBERLINE</div>
  <div class="abs card" style="left:393px;top:446px">DISONA</div>
  <div class="abs card" style="left:443px;top:446px">MINTCARD</div>
  <div class="abs card" style="left:493px;top:446px">PAYWELL</div>

  <span class="abs label" style="top:500px">Expiration Date</span>
  <div class="abs field" style="left:291px;top:488px;width:67px;height:32px">MM</div>
  <div class="abs field" style="left:365px;top:488px;width:68px;height:32px">YY</div>

  <span class="abs label" style="top:539px">CSV</span>
  <div class="abs field" style="left:290px;top:529px;width:97px;height:31px"></div>

  <span class="abs label" style="top:580px">Last Name</span>
  <div class="abs field" style="left:290px;top:570px;width:330px;height:32px"></div>

  <span class="abs label" style="top:620px">First Name</span>
  <div class="abs field" style="left:290px;top:611px;width:330px;height:31px"></div>

  <span class="abs label" style="top:660px">Postal code</span>
  <div class="abs field" style="left:289px;top:652px;width:111px;height:31px"></div>
  <div class="abs field" style="left:407px;top:652px;width:111px;height:31px"></div>

  <div class="abs btn" style="left:290px;top:710px;width:101px;height:38px">Proceed</div>

  <div class="abs divider"></div>

  <h2 class="abs side-title">Already have a account?</h2>
  <span class="abs side-label" style="left:706px;top:362px">Email</span>
  <div class="abs field" style="left:706px;top:381px;width:270px;height:31px"></div>
  <span class="abs side-label" style="left:706px;top:426px">Password</span>
  <div class="abs field" style="left:707px;top:449px;width:271px;height:32px"></div>
  <div class="abs btn" style="left:706px;top:490px;width:100px;height:38px">Log In</div>
  <span class="abs forgot">Forgot email or password?</span>

  <footer class="abs footer">
    <div class="footer-nav">
      <a style="left:127px" href="#">HOME</a>
      <a style="left:212px" href="#">VOSTRELLEN</a>
      <a style="left:363px" href="#">OUR COURSES</a>
      <a style="left:509px" href="#">LET'S CHAT</a>
      <a style="left:635px" href="#">ABOUT QUORVANA</a>
    </div>
    <p class="copyright">© 2016 Company Name &nbsp;All right reserved &nbsp;Term of Use</p>
    <div class="social" aria-label="Social links"><span></span><span></span><span></span><span></span></div>
  </footer>

</div>
</body>
</html>
```